Business Card for Polygraph business in Africa

Business Card . Polygraph Examiner based in Tanzania, East Africa.
Business Card will be used to disseminate contact information to potential clients.
It should convey that I am a professional specifically in the polygraph field and perform my work with integrity.

I have attached the business card that I'm currently using, which I threw together myself initially. It's not professional enough.

Target Market(s)

Banks, Accounting Firms, Government Ministries, Gas, Oil, & Gemstone Mining Concerns, Wildlife Conservation NGOs, International companies located in East Africa.

Industry/Entity Type

Business

Contact Information for Business Card

Veritrace Kilonga
Miriam Holloway
PO Box 48317
Arusha, Tanzania
+255 612 839 274
miriamholloway@postvale.example

Colors
00a990
f37122
faa54b

Requirements
Must have
• - Veritrace Kilonga (with the word "Polygraph" being more prominent than the word "Tanzania")
• - Forensic Examinations
• - Employment Screening
• - Should contain a logo of the Continental Truthline Society (of which I'm a member)
• - I would like an accent design (such as the polygraph "squiggles" of a cardio tracing or such as that)
• - My contact information (less prominent, but large enough to read legibly). I would also consider putting the contact information on the second side of the card.
Nice to have
• My color suggestions are changeable.
Should not have
• Anything "cutesy" or "cartoonish"

```html
<!DOCTYPE html>
<html lang="en">
<head>
<meta charset="utf-8">
<title>Veritrace Kilonga – Business Card</title>
<link rel="stylesheet" href="https://fonts.googleapis.com/css2?family=Open+Sans:wght@400;600;700&display=swap">
<style>
  :root {
    --teal: #00a990;
    --orange: #f37122;
    --apricot: #faa54b;
    --ink: #4a4a4a;
    --muted: #7a7a7a;
    --paper: #ffffff;
    --backdrop: #eeeeee;
    --seal-ring: #2d3a7a;
  }
  * { box-sizing: border-box; margin: 0; padding: 0; }
  html, body {
    width: 1200px; height: 900px; overflow: hidden;
    background: var(--backdrop);
    font-family: "Open Sans", Arial, sans-serif;
  }
  .stage {
    width: 1200px; height: 900px;
    display: flex; align-items: center; justify-content: center; gap: 50px;
  }
  .card {
    width: 525px; height: 300px; position: relative; overflow: hidden;
    box-shadow: 0 6px 18px rgba(0,0,0,.12);
  }

  /* Front */
  .card--front { background: var(--paper); }
  .holder { position: absolute; left: 34px; top: 30px; }
  .holder__name { font-size: 17px; font-weight: 700; letter-spacing: .5px; text-transform: uppercase; }
  .holder__first { color: var(--teal); }
  .holder__last { color: var(--apricot); }
  .holder__role { font-size: 10px; color: var(--muted); margin-top: 1px; }

  .contact { position: absolute; left: 34px; top: 96px; font-size: 11px; line-height: 1.6; color: var(--ink); }
  .contact__row { display: flex; align-items: center; gap: 6px; }
  .contact__row svg { width: 10px; height: 10px; flex: none; }
  .contact__indent { padding-left: 0; }

  .brand { font-weight: 700; white-space: nowrap; }
  .card--front .brand {
    position: absolute; left: 200px; top: 170px;
    font-size: 26px; color: var(--teal);
    padding-bottom: 3px; border-bottom: 1.5px solid var(--teal);
  }

  .services {
    position: absolute; right: 32px; bottom: 26px;
    list-style: none; text-align: right; font-size: 12px; color: var(--ink); line-height: 1.55;
  }
  .services li::after {
    content: ""; display: inline-block; width: 6px; height: 6px; border-radius: 50%;
    background: var(--apricot); margin-left: 8px; vertical-align: middle;
  }

  /* Back */
  .card--back { display: flex; flex-direction: column; }
  .band { flex: 1; position: relative; }
  .band--teal { background: var(--teal); }
  .band--orange { background: var(--apricot); }
  .card--back .brand {
    position: absolute; left: 50%; bottom: 18px; transform: translateX(-50%);
    font-size: 26px; color: var(--paper);
    padding-bottom: 3px; border-bottom: 1.5px solid var(--paper);
  }
  .seal {
    position: absolute; left: 50%; top: 50%; transform: translate(-50%, -50%);
    width: 96px; height: 96px;
  }
</style>
</head>
<body>
<main class="stage">

  <section class="card card--front" aria-label="Business card front">
    <div class="holder">
      <p class="holder__name"><span class="holder__first">Miriam</span> <span class="holder__last">Holloway</span></p>
      <p class="holder__role">Owner</p>
    </div>

    <address class="contact">
      <p class="contact__row">PO Box 48317</p>
      <p class="contact__row">Arusha, Tanzania</p>
      <p class="contact__row">
        <svg viewBox="0 0 10 10" aria-hidden="true"><path fill="var(--teal)" d="M2 0.5 L3.6 2.6 L2.8 3.6 Q4 6 6.4 7.2 L7.4 6.4 L9.5 8 L8.4 9.5 Q3.5 9 0.5 1.6 Z"/></svg>
        +255 612 839 274
      </p>
      <p class="contact__row">
        <svg viewBox="0 0 10 10" aria-hidden="true"><rect x="0.5" y="2" width="9" height="6.5" rx="1" fill="var(--teal)"/><path d="M1 2.6 L5 5.6 L9 2.6" fill="none" stroke="#fff" stroke-width="0.9"/></svg>
        miriamholloway@postvale.example
      </p>
    </address>

    <p class="brand">Veritrace Kilonga</p>

    <ul class="services">
      <li>Forensic Examinations</li>
      <li>Employment Screening</li>
    </ul>
  </section>

  <section class="card card--back" aria-label="Business card back">
    <div class="band band--teal">
      <p class="brand">Veritrace Kilonga</p>
    </div>
    <div class="band band--orange">
      <svg class="seal" viewBox="0 0 96 96" role="img" aria-label="Continental Truthline Society membership badge">
        <circle cx="48" cy="48" r="45" fill="var(--paper)" stroke="var(--seal-ring)" stroke-width="3"/>
      </svg>
    </div>
  </section>

</main>
</body>
</html>
```